Irrigation Business needs their business cards modernised and revamped

I would like to keep my current logo, colours and revamp the format of the card.

I would like the card to be clean yet important.

Im not sure if you include texture but i would like the named logo to be indented into the card etc.

show me something alive and free something thats clinical to the point yet has a feel of achievement. i would like people to go nice card.

Target Market(s)

high end clients, corporate, sports field manger, the guys that make the decisions

Industry/Entity Type

Business

Contact Information for Business Card

nformation to be included

Dean Harlow (Director)
0487305526
dean@kolvat.biz
www.kestonfieldworks.com

instagram logo
google logo
facebook logo

Colors

Designer to choose colors to be used in the design.

Requirements
Nice to have
• indentations a really nice feel to the card good texture

```html
<!DOCTYPE html>
<html lang="en">
<head>
<meta charset="utf-8">
<title>Keston Fieldworks — Business Card</title>
<link href="https://fonts.googleapis.com/css2?family=Roboto+Condensed:wght@700&family=Roboto:wght@400&family=Arimo:wght@700&display=swap" rel="stylesheet">
<style>
  :root {
    --backdrop: #2a2a2a;
    --sky: #2ea3cf;
    --deep: #2e66a6;
    --paper: #f3f3f3;
    --white: #ffffff;
  }
  * { margin: 0; padding: 0; box-sizing: border-box; }
  html, body { width: 1200px; height: 960px; overflow: hidden; }
  body { background: var(--backdrop); position: relative; font-family: "Roboto", sans-serif; }

  .card {
    position: absolute;
    width: 600px;
    height: 343px;
    overflow: hidden;
  }
  .card--front { left: 314px; top: 113px; background: var(--sky); color: var(--white); }
  .card--back { left: 311px; top: 472px; background: var(--paper); }

  .holder { position: absolute; left: 50px; top: 48px; }
  .holder__name {
    font-family: "Roboto Condensed", sans-serif;
    font-weight: 700;
    font-size: 21px;
    letter-spacing: 0.2px;
    line-height: 24px;
  }
  .holder__role {
    font-family: "Roboto Condensed", sans-serif;
    font-weight: 700;
    font-size: 15px;
    line-height: 20px;
    opacity: 0.95;
  }
  .social { display: flex; gap: 3px; margin-top: 10px; }
  .social__dot { width: 26px; height: 26px; border-radius: 50%; background: var(--white); }

  .contact { position: absolute; left: 50px; top: 242px; list-style: none; }
  .contact__item {
    display: flex; align-items: center; gap: 8px;
    font-size: 14px; line-height: 19px;
  }
  .contact__icon { width: 14px; height: 14px; flex: none; }

  .stripes { position: absolute; right: 0; top: 0; width: 170px; height: 343px; }

  .brand {
    position: absolute; left: 0; right: 0; top: 80px;
    display: flex; flex-direction: column; align-items: center; gap: 28px;
  }
  .brand__mark { width: 106px; height: 106px; border-radius: 50%; background: var(--deep); }
  .brand__name {
    font-family: "Arimo", sans-serif;
    font-weight: 700;
    font-size: 33px;
    letter-spacing: -0.5px;
    color: var(--deep);
    text-transform: uppercase;
  }
</style>
</head>
<body>

<section class="card card--front">
  <div class="holder">
    <h1 class="holder__name">DEAN HARLOW</h1>
    <p class="holder__role">DIRECTOR</p>
    <div class="social" aria-label="Social profiles">
      <span class="social__dot"></span>
      <span class="social__dot"></span>
      <span class="social__dot"></span>
    </div>
  </div>

  <ul class="contact">
    <li class="contact__item">
      <svg class="contact__icon" viewBox="0 0 24 24" aria-hidden="true"><path fill="#fff" d="M6.6 10.8a15.2 15.2 0 0 0 6.6 6.6l2.2-2.2c.3-.3.7-.4 1-.2 1.1.4 2.3.6 3.6.6.6 0 1 .4 1 1V20c0 .6-.4 1-1 1A17 17 0 0 1 3 4c0-.6.4-1 1-1h3.5c.6 0 1 .4 1 1 0 1.3.2 2.5.6 3.6.1.3 0 .7-.2 1z"/></svg>
      <span>0487305526</span>
    </li>
    <li class="contact__item">
      <svg class="contact__icon" viewBox="0 0 24 24" aria-hidden="true"><path fill="#fff" d="M2 5h20v14H2z"/><path fill="none" stroke="#2ea3cf" stroke-width="2" d="M2 6l10 7 10-7"/></svg>
      <span>dean@kolvat.biz</span>
    </li>
    <li class="contact__item">
      <svg class="contact__icon" viewBox="0 0 24 24" aria-hidden="true"><circle cx="12" cy="12" r="10" fill="#fff"/><path fill="none" stroke="#2ea3cf" stroke-width="1.6" d="M2 12h20M12 2c3 3 3 17 0 20M12 2c-3 3-3 17 0 20"/></svg>
      <span>www.kestonfieldworks.com</span>
    </li>
  </ul>

  <svg class="stripes" viewBox="0 0 170 343" aria-hidden="true">
    <rect width="170" height="343" fill="#2e66a6"/>
    <g stroke="#fff" stroke-width="3">
      <line x1="0" y1="12" x2="170" y2="12"/>
      <line x1="0" y1="33" x2="170" y2="33"/>
      <line x1="0" y1="54" x2="170" y2="54"/>
      <line x1="0" y1="75" x2="170" y2="75"/>
      <line x1="0" y1="96" x2="170" y2="96"/>
      <line x1="0" y1="117" x2="170" y2="117"/>
      <line x1="0" y1="138" x2="170" y2="138"/>
      <line x1="0" y1="159" x2="170" y2="159"/>
      <line x1="0" y1="180" x2="170" y2="180"/>
      <line x1="0" y1="201" x2="170" y2="201"/>
      <line x1="0" y1="222" x2="170" y2="222"/>
      <line x1="0" y1="243" x2="170" y2="243"/>
      <line x1="0" y1="264" x2="170" y2="264"/>
      <line x1="0" y1="285" x2="170" y2="285"/>
      <line x1="0" y1="306" x2="170" y2="306"/>
      <line x1="0" y1="327" x2="170" y2="327"/>
    </g>
  </svg>
</section>

<section class="card card--back">
  <div class="brand">
    <span class="brand__mark"></span>
    <p class="brand__name">Keston Fieldworks</p>
  </div>
</section>

</body>
</html>
```